Psychology service brochure

Marketing brochure for a new psychological counselling service.
Our old brochure was too boring and conservative. We are selling our services to GP's, psychiatrists, other health providers and of course potential clients. We'd really like a professional, elegant look that conveys us to be compassionate and conscientious providers of psychological services.
I have included a copy of our old brochure and a copy of the changes we'd like to the text.
Updates
I have included a photo of myself and my business partner. Only the faces are needed, so backgrounds would need to be edited out.
Hello, in consultation with my business partner, we would like
the use of our photos in the brochure please (with backgrounds edited out)
no stock photos of random people
use of abstract or nature/floral motifs suggestive of tranquillity
regards,
Rosalind
Target Market(s)
General practitioner doctors, potential clients
Industry/Entity Type
Health
Requirements
Must have
- must include BlairMdITC TT- font for the business name
- must include our signature color Pantone 291 (see attached brochure)
- use of the photos of myself and my business partner (with background edited out please)
- keep use of colours to a minimum, 3 colors maximum, one of which must be Pantone 291
- must include changes to the brochure as outlined in the 'Changes to Pamphlet' document.
Nice to have
- an interesting, eye catching layout.
- interesting use of white spaces
- use of subtle abstract or nature/floral related graphics suggestive of tranquillity
Should not have
- should not include our fee
- stock photos of people

```html
<!DOCTYPE html>
<html lang="en">
<head>
<meta charset="utf-8">
<title>Stillwater Mind Counselling – Brochure</title>
<link rel="stylesheet" href="https://fonts.googleapis.com/css2?family=Arimo:wght@400;700&display=swap">
<style>
  :root {
    --ink: #4fd9ec;
    --tint: #b3f2fa;
    --tint-soft: #d4f8fc;
    --paper: #ffffff;
    --stage: #ffffff;
  }
  * { margin: 0; padding: 0; box-sizing: border-box; }
  html, body { width: 1200px; height: 900px; overflow: hidden; background: var(--stage); }
  body { font-family: "Arimo", Arial, sans-serif; color: var(--ink); }

  .brochure {
    position: absolute; left: 105px; top: 92px; width: 984px; height: 702px;
    background: var(--paper);
    box-shadow: 3px 4px 6px rgba(0,0,0,0.45);
  }
  .brochure > * { position: absolute; }

  .edge-strip { left: 0; top: 0; width: 18px; height: 100%; background: var(--tint); }

  .section-heading {
    left: 19px; width: 247px; height: 54px;
    background: var(--tint); color: var(--paper);
    font-weight: 700; font-size: 15.5px; line-height: 20px; letter-spacing: 0.6px;
    padding: 11px 0 0 36px; text-transform: uppercase;
  }
  .heading-rule { left: 19px; width: 306px; height: 4px; background: var(--tint); }

  .approach-heading { top: 51px; }
  .approach-rule { top: 104px; }
  .clients-heading { top: 340px; }
  .clients-rule { top: 394px; }

  .body-copy { left: 55px; width: 210px; font-size: 12px; line-height: 13.6px; }
  .body-copy p + p { margin-top: 6px; }
  .approach-copy { top: 122px; }

  .client-goals { top: 411px; left: 55px; width: 200px; list-style: none; font-size: 12px; line-height: 13.6px; }
  .client-goals li { position: relative; padding-left: 13px; margin-bottom: 6px; }
  .client-goals li::before {
    content: ""; position: absolute; left: 1px; top: 5px;
    width: 4px; height: 4px; border-radius: 50%; background: var(--ink);
  }

  .location-map {
    left: 352px; top: 105px; width: 271px; height: 274px;
    background: linear-gradient(135deg, #f2fdfe, var(--tint-soft));
    border: 1px solid var(--tint);
    box-shadow: 2px 2px 4px rgba(79,217,236,0.3);
  }

  .contact-panel {
    left: 325px; top: 458px; width: 323px; height: 159px;
    background: var(--tint); color: var(--paper); font-size: 12px;
  }
  .contact-title { position: absolute; top: 22px; left: 0; width: 100%; text-align: center; padding-left: 12px; }
  .contact-venue { position: absolute; top: 42px; left: 0; width: 100%; text-align: center; padding-left: 12px; font-weight: 700; }
  .contact-address { position: absolute; top: 63px; left: 0; width: 100%; text-align: center; padding-left: 12px; }
  .contact-lines {
    position: absolute; top: 83px; left: 20px;
    display: grid; grid-template-columns: 83px auto; column-gap: 6px; row-gap: 6.5px;
  }
  .contact-lines dt { text-align: right; }
  .contact-lines dd { font-weight: 700; }

  .sky-panel {
    left: 648px; top: 0; width: 257px; height: 100%;
    background: radial-gradient(ellipse at 75% 12%, #e4fbfe 0%, transparent 35%),
                radial-gradient(ellipse at 35% 65%, #dcfafd 0%, transparent 40%),
                var(--tint);
  }

  .cover-spine { left: 905px; top: 0; width: 79px; height: 100%; }
  .business-name {
    position: absolute; left: 50%; top: 50%;
    transform: translate(-50%, -50%) rotate(-90deg);
    white-space: nowrap; font-size: 27px; letter-spacing: 2.4px; text-transform: uppercase;
    color: var(--tint);
  }
</style>
</head>
<body>
  <article class="brochure">
    <div class="edge-strip"></div>

    <h2 class="section-heading approach-heading">Our approach<br>to therapy</h2>
    <div class="heading-rule approach-rule"></div>
    <div class="body-copy approach-copy">
      <p>We are warm, compassionate and professional Clinical General Psychologists who together have thirty years of experience and who are committed to providing high quality evidence-based treatment to our clients.</p>
      <p>Types of treatment may include Cognitive Behavioural Therapy, Motivational Interviewing and Mindfulness.</p>
    </div>

    <h2 class="section-heading clients-heading">What we want<br>for our clients</h2>
    <div class="heading-rule clients-rule"></div>
    <ul class="client-goals">
      <li>For you to feel heard and respected</li>
      <li>To have a positive experience of working collaboratively with a psychologist</li>
      <li>To connect or reconnect with feelings of hope</li>
      <li>To move beyond counselling with an understanding of your strengths and the skills to make changes that will help you to meet future challenges.</li>
    </ul>

    <div class="location-map" role="img" aria-label="Street map showing the centre's location near the railway station"></div>

    <section class="contact-panel">
      <p class="contact-title">Contact reception</p>
      <p class="contact-venue">THE LARKFIELD CENTRE</p>
      <p class="contact-address">18 Larkfield Street, Easton 3091</p>
      <dl class="contact-lines">
        <dt>Phone:</dt><dd>5550 1234</dd>
        <dt>Fax:</dt><dd>5550 5678</dd>
        <dt>Email:</dt><dd>hello@stillwatermind.com</dd>
      </dl>
    </section>

    <div class="sky-panel" role="img" aria-label="Soft pale blue sky with drifting clouds"></div>

    <div class="cover-spine">
      <h1 class="business-name">Stillwater Mind Counselling</h1>
    </div>
  </article>
</body>
</html>
```